Business card for Eyelash extension salon in Beverly Hills,California USA

We need new business card for our salon in Beverly Hills. The salon name is 'Lashvera' . We would like to have...Business name: Lashvera Name of person: will provide later Address 4720 N.Alder Crest Ave Beverly Hills , CA 90210 Phone: will provide later (Text only) Web: www.lashverastudio.example Snapgrid icon, Circlebook icon follow us for seasonal campaign and news @lashverastudiolounge Design should look elegant, high-end, clean, simple, cohesive with my brand. Please refer my brand board. Business name color will be metallic bronzy color. Im thinking grey background or white background. Thanks

Target Market(s)

25-35. Gender neutral. People who are in Entertainment business industry.
This is High-end Eyelash extension salon in Beverly Hills

Industry/Entity Type

Beauty Salon

Contact Information for Business Card

Business name: Lashvera
Name of person: will provide later
Address 4720 N.Alder Crest Ave Beverly Hills , CA 90210
Phone: will provide later (Text only)
Web: www.lashverastudio.example
Snapgrid icon, Circlebook icon
follow us for seasonal campaign and news @lashverastudiolounge

Requirements
Must have
• Beautiful, elegant, clean and simple look but very attractive and modern
Should not have
• We don't like too clutter, too busy designs.

```html
<!DOCTYPE html>
<html lang="en">
<head>
<meta charset="utf-8">
<title>Lashvera Business Card</title>
<link rel="stylesheet" href="https://fonts.googleapis.com/css2?family=Montserrat:wght@300;400;500;600&display=swap">
<style>
  :root {
    --stage: #2b2b2d;
    --bronze: #8c6a52;
    --bronze-light: #a3826a;
    --bronze-dark: #7f5e48;
    --paper: #ffffff;
    --ink: #1f1f1f;
    --ink-soft: #3a3a3a;
    --white: #ffffff;
  }
  * { margin: 0; padding: 0; box-sizing: border-box; }
  html, body {
    width: 1200px; height: 900px; overflow: hidden;
    background: var(--stage);
    font-family: "Montserrat", sans-serif;
  }
  .canvas { position: relative; width: 1200px; height: 900px; }

  .card {
    position: absolute;
    width: 700px; height: 400px;
    border-radius: 22px;
    overflow: hidden;
  }

  /* Front */
  .card-front {
    left: 110px; top: 45px;
    background: linear-gradient(135deg, var(--bronze-dark) 0%, var(--bronze) 55%, var(--bronze-light) 100%);
    color: var(--white);
  }
  .brand {
    position: absolute;
    right: 90px; top: 120px;
    text-align: right;
  }
  .brand-name {
    font-size: 62px; font-weight: 300; letter-spacing: 2px; line-height: 1;
  }
  .brand-place {
    margin-top: 10px;
    font-size: 11px; font-weight: 400; letter-spacing: 4px;
  }
  .front-social {
    position: absolute; left: 48px; bottom: 48px;
    display: flex; align-items: center; gap: 14px;
    font-size: 14px; font-weight: 400;
  }
  .network { font-size: 12px; font-weight: 500; }

  /* Back */
  .card-back {
    left: 390px; top: 470px;
    background: var(--paper);
    color: var(--ink);
  }
  .person {
    position: absolute; left: 44px; top: 56px;
  }
  .person-name {
    font-size: 26px; font-weight: 500; letter-spacing: 2px;
    color: var(--bronze);
  }
  .person-role {
    margin-top: 6px;
    font-size: 11px; font-weight: 600; letter-spacing: 1.5px;
    color: var(--ink);
  }
  .website {
    position: absolute; right: 22px; top: 36px;
    writing-mode: vertical-rl;
    font-size: 17px; font-weight: 400; letter-spacing: 3px;
    color: var(--bronze);
  }
  .contact {
    position: absolute; left: 44px; bottom: 40px;
    font-size: 16px; font-weight: 400; line-height: 1.3;
    color: var(--ink-soft);
  }
  .contact p + p { margin-top: 2px; }
  .contact .address { margin-top: 12px; }
  .tel-label { color: var(--bronze-light); font-weight: 300; }
  .back-social {
    margin-top: 16px;
    display: flex; align-items: center; gap: 14px;
    font-size: 14px;
  }
  .back-social .network { color: var(--ink-soft); }
  .back-social .handle { color: var(--bronze); }
</style>
</head>
<body>
<main class="canvas">

  <section class="card card-front">
    <div class="brand">
      <div class="brand-name">Lashvera</div>
      <div class="brand-place">BEVERLY HILLS</div>
    </div>
    <div class="front-social">
      <span class="network">Snapgrid</span>
      <span class="network">Circlebook</span>
      <span class="handle">@lashverastudiolounge</span>
    </div>
  </section>

  <section class="card card-back">
    <div class="person">
      <h1 class="person-name">ELENA &amp; NOORA</h1>
      <div class="person-role">WEEDING PLANNER</div>
    </div>
    <div class="website">lashverastudio.example</div>
    <div class="contact">
      <p><span class="tel-label">TEL/</span>503-555-0147</p>
      <p>elena@mail.example</p>
      <p class="address">4720 N.Alder Crest Ave<br>Beverly Hills , CA 90210</p>
      <div class="back-social">
        <span class="network">Snapgrid</span>
        <span class="network">Circlebook</span>
        <span class="handle">@lashvera</span>
      </div>
    </div>
  </section>

</main>
</body>
</html>
```